Design 4 pages for an event discovery website

This is a contest for the design of 4 pages for an events discovery website. The feature is part of the new sign-up process.

Please see the attached document for a full scope, mockups and the parent category icons.

Target Market(s)

18-35 Australian event goers

Industry/Entity Type

Events

Number of Pages Required

4 page

```html
<!DOCTYPE html>
<html lang="en">
<head>
<meta charset="utf-8">
<title>Gathero – Sign up</title>
<link rel="stylesheet" href="https://fonts.googleapis.com/css2?family=Oswald:wght@300;400&family=Nunito+Sans:wght@300;400&family=Roboto:ital,wght@0,500;1,300&display=swap">
<style>
  :root {
    --brand: #13b5da;
    --white: #ffffff;
    --heading: #5f5f5f;
    --text: #333333;
    --social: #3b55a0;
    --rule: #dcdcdc;
    --search-ring: #8fdcef;
    --search-text: #8a8a8a;
  }
  * { box-sizing: border-box; margin: 0; padding: 0; }
  html, body { width: 1200px; height: 494px; overflow: hidden; background: var(--white); }
  body { position: relative; font-family: "Nunito Sans", sans-serif; color: var(--text); }

  .site-header {
    position: absolute; left: 0; top: 0; width: 1200px; height: 71px;
    background: var(--brand); color: var(--white);
  }
  .brand-name {
    position: absolute; left: 75px; top: 6px;
    font-family: "Oswald", sans-serif; font-weight: 400; font-size: 42px; line-height: 56px;
    color: var(--white); letter-spacing: 0.5px;
  }
  .main-nav, .account-nav {
    position: absolute; top: 27px; display: flex; gap: 10px;
    font-family: "Roboto", sans-serif; font-weight: 500; font-size: 12.5px; line-height: 16px;
    letter-spacing: 0.4px;
  }
  .main-nav { left: 258px; }
  .account-nav { left: 1016px; }
  .nav-sep { opacity: 0.9; }
  .search-box {
    position: absolute; left: 800px; top: 20px; width: 197px; height: 31px;
    background: var(--white); border: 2px solid var(--search-ring); border-radius: 16px;
  }
  .search-placeholder {
    position: absolute; left: 18px; top: 6px;
    font-family: "Roboto", sans-serif; font-style: italic; font-weight: 300; font-size: 14px;
    color: var(--search-text);
  }
  .search-icon { position: absolute; right: 9px; top: 6px; }

  .section-title {
    position: absolute; top: 128px;
    font-family: "Oswald", sans-serif; font-weight: 300; font-size: 37px; line-height: 44px;
    color: var(--heading); letter-spacing: 0.2px;
  }
  .signup-title { left: 75px; }
  .advantage-title { left: 524px; }

  .social-connect {
    position: absolute; left: 75px; top: 186px; width: 330px; height: 127px;
    background: var(--social); border-radius: 18px; color: var(--white);
  }
  .social-connect-label {
    position: absolute; left: 119px; top: 32px;
    font-family: "Nunito Sans", sans-serif; font-weight: 300; font-size: 28px; line-height: 33px;
  }

  .advantage-list { position: absolute; left: 524px; top: 180px; list-style: none; }
  .advantage-list li {
    display: flex; align-items: center; height: 30.4px;
    font-size: 16px; font-weight: 400; color: var(--text);
  }
  .advantage-list svg { margin-right: 12px; flex: none; }

  .divider { position: absolute; left: 75px; top: 390px; width: 1052px; height: 1px; background: var(--rule); }

  .alt-signup { position: absolute; left: 75px; top: 414px; font-size: 16px; color: var(--text); }
  .alt-signup a { color: var(--social); text-decoration: none; }
</style>
</head>
<body>
  <header class="site-header">
    <div class="brand-name">Gathero</div>
    <nav class="main-nav"><span>FIND</span><span class="nav-sep">|</span><span style="margin-left:6px">EVENTS</span></nav>
    <div class="search-box">
      <span class="search-placeholder">Search..</span>
      <svg class="search-icon" width="20" height="16" viewBox="0 0 20 16">
        <circle cx="7" cy="6.5" r="4.6" fill="none" stroke="#555" stroke-width="2"/>
        <line x1="10.5" y1="9.5" x2="17" y2="14" stroke="#555" stroke-width="3" stroke-linecap="round"/>
      </svg>
    </div>
    <nav class="account-nav"><span>SIGN UP</span><span class="nav-sep">|</span><span>LOG IN</span></nav>
  </header>

  <h1 class="section-title signup-title">SIGN UP</h1>
  <div class="social-connect">
    <div class="social-connect-label">Connect<br>with Matesnet</div>
  </div>

  <h2 class="section-title advantage-title">ADVANTAGE</h2>
  <ul class="advantage-list">
    <li><svg width="14" height="12" viewBox="0 0 14 12"><path d="M1 6.5 L5 10.5 L13 1.5" fill="none" stroke="#13b5da" stroke-width="2.6" stroke-linejoin="round"/></svg>Get personalised event recommendations</li>
    <li><svg width="14" height="12" viewBox="0 0 14 12"><path d="M1 6.5 L5 10.5 L13 1.5" fill="none" stroke="#13b5da" stroke-width="2.6" stroke-linejoin="round"/></svg>Get notified about your favourite events – never miss out again</li>
    <li><svg width="14" height="12" viewBox="0 0 14 12"><path d="M1 6.5 L5 10.5 L13 1.5" fill="none" stroke="#13b5da" stroke-width="2.6" stroke-linejoin="round"/></svg>Follow all your favourite artists, musicians, teams and players in one place</li>
    <li><svg width="14" height="12" viewBox="0 0 14 12"><path d="M1 6.5 L5 10.5 L13 1.5" fill="none" stroke="#13b5da" stroke-width="2.6" stroke-linejoin="round"/></svg>Follow your favourite local venues to know everything happening there</li>
    <li><svg width="14" height="12" viewBox="0 0 14 12"><path d="M1 6.5 L5 10.5 L13 1.5" fill="none" stroke="#13b5da" stroke-width="2.6" stroke-linejoin="round"/></svg>Get curated news and feature content on your favourite artists (coming soon)</li>
    <li><svg width="14" height="12" viewBox="0 0 14 12"><path d="M1 6.5 L5 10.5 L13 1.5" fill="none" stroke="#13b5da" stroke-width="2.6" stroke-linejoin="round"/></svg>Invite your mates to events via Matesnet (MN sign-up only)</li>
  </ul>

  <div class="divider"></div>
  <p class="alt-signup">Or Click here to sign up without <a href="#">MATESNET</a></p>
</body>
</html>
```